Logo, Web and Mobile Designs for enterprise social media platform

All the details are in the attached document, please start reading the scope document first which explains what is this project about and the details about the needed deliverables, after that please read the UI_Requirements document which will detail what is expected regarding the coded web version since this is a coded contest, it is very important that you meet the UI requirements or suggest something else but we will need to agree first before working on the coded version

Good Luck

Target Market(s)

Enterprise Social Media

Industry/Entity Type

Media

Coding

Coded - Design and coding required

Number of Pages Required

5+ page

Font styles to use
Sans Serif

Requirements
Must have
• All the must haves are listed in the scope document so please check before you start

```html
<!DOCTYPE html>
<html lang="en">
<head>
<meta charset="utf-8">
<title>Teamora – Track Details</title>
<link href="https://fonts.googleapis.com/css2?family=Open+Sans:wght@400;600;700&display=swap" rel="stylesheet">
<style>
:root{
  --page-bg:#efefef;
  --header-bg:#fafafa;
  --line:#dedede;
  --item-bg:#f4f4f5;
  --text:#3d3f44;
  --muted:#8c8f94;
  --blue:#1f86c6;
  --blue-dark:#1a73ac;
  --footer:#2a8fc0;
  --error:#e0242c;
  --brand:#2d9fd6;
  --accent:#f39a1c;
}
*{box-sizing:border-box;margin:0;padding:0}
html,body{width:1200px;height:3420px;overflow:hidden}
body{background:var(--page-bg);font-family:"Open Sans",Arial,sans-serif;color:var(--text);position:relative}
.app-header{position:absolute;left:0;top:0;width:1200px;height:288px;background:linear-gradient(#ffffff,#f1f1f1);border-bottom:4px solid var(--line);display:flex;align-items:center;justify-content:space-between}
.header-cell{width:220px;height:100%;display:flex;align-items:center;justify-content:center}
.header-cell.home{border-right:4px solid var(--line)}
.header-cell.menu{border-left:4px solid var(--line)}
.brand{display:flex;align-items:center;gap:22px}
.brand-dot{width:92px;height:92px;border-radius:50%;background:var(--accent)}
.brand-name{font-size:78px;font-weight:600;color:var(--brand);letter-spacing:1px}
.nav-panel{position:absolute;left:44px;top:312px;width:1112px;background:#fff;border:4px solid var(--line)}
.nav-item{height:150px;display:flex;align-items:center;padding:0 60px 0 72px;background:var(--item-bg);border-bottom:4px solid #e4e4e4;font-size:42px;text-transform:uppercase;color:var(--text)}
.nav-item .icon{width:48px;margin-right:60px;display:flex;justify-content:center}
.nav-item .label{flex:1}
.track-body{height:948px;background:#fff;padding:82px 44px 0;border-bottom:4px solid #e4e4e4}
.track-card{height:708px;border:4px solid var(--line);background:#fff}
.card-head{height:144px;background:var(--item-bg);border-bottom:4px solid var(--line);display:flex;align-items:center;padding-left:60px;font-size:46px;text-transform:uppercase;color:var(--text);gap:22px}
.card-body{padding:112px 60px 0 64px}
.field-label{font-size:42px;color:var(--text)}
.field-input{margin-top:38px;width:896px;height:112px;border:4px solid #e2e2e2;display:flex;align-items:center;padding-left:40px;font-size:30px;color:var(--error)}
.btn-add{margin-top:56px;width:436px;height:104px;background:var(--blue);border:none;border-bottom:6px solid var(--blue-dark);color:#fff;font-family:inherit;font-weight:600;font-size:44px;text-transform:uppercase;display:flex;align-items:center;justify-content:center}
.site-footer{position:absolute;left:0;top:3048px;width:1200px;height:372px;background:var(--footer);color:#fff;text-align:center}
.social-row{display:flex;justify-content:center;gap:30px;padding-top:84px}
.social-row span{width:60px;height:60px;background:#fff;border-radius:8px}
.footer-links{margin-top:40px;font-size:34px;font-weight:600;word-spacing:4px}
.footer-links .sep{margin:0 16px}
.copyright{margin-top:22px;font-size:33px;font-weight:600}
</style>
</head>
<body>
<header class="app-header">
  <div class="header-cell home">
    <svg width="54" height="48" viewBox="0 0 54 48"><path d="M27 2 L52 24 H45 V46 H33 V32 H21 V46 H9 V24 H2 Z" fill="#666"/></svg>
  </div>
  <div class="brand"><span class="brand-dot"></span><span class="brand-name">Teamora</span></div>
  <div class="header-cell menu">
    <svg width="54" height="44" viewBox="0 0 54 44"><rect y="0" width="54" height="8" rx="2" fill="#666"/><rect y="18" width="54" height="8" rx="2" fill="#666"/><rect y="36" width="54" height="8" rx="2" fill="#666"/></svg>
  </div>
</header>

<nav class="nav-panel">
  <div class="nav-item"><span class="icon"><svg width="44" height="44" viewBox="0 0 44 44" fill="#1f86c6"><rect width="20" height="20" rx="3"/><rect x="24" width="20" height="20" rx="3"/><rect y="24" width="20" height="20" rx="3"/><rect x="24" y="24" width="20" height="20" rx="3"/></svg></span><span class="label">View Dashboard</span></div>
  <div class="nav-item"><span class="icon"><svg width="44" height="44" viewBox="0 0 44 44" fill="none" stroke="#1f86c6" stroke-width="4"><rect x="3" y="7" width="38" height="34" rx="3"/><line x1="3" y1="17" x2="41" y2="17"/><line x1="13" y1="2" x2="13" y2="11"/><line x1="31" y1="2" x2="31" y2="11"/><path d="M11 24h4M20 24h4M29 24h4M11 32h4M20 32h4M29 32h4"/></svg></span><span class="label">View Event</span><svg class="chev" width="24" height="26" viewBox="0 0 24 26" fill="none" stroke="#999" stroke-width="4"><path d="M3 12l9-9 9 9M3 23l9-9 9 9"/></svg></div>
  <div class="nav-item"><span class="icon"><svg width="18" height="30" viewBox="0 0 18 30" fill="none" stroke="#1f86c6" stroke-width="5"><path d="M3 3l12 12L3 27"/></svg></span><span class="label">About Us</span><svg width="24" height="26" viewBox="0 0 24 26" fill="none" stroke="#999" stroke-width="4"><path d="M3 12l9-9 9 9M3 23l9-9 9 9"/></svg></div>
  <div class="nav-item"><span class="icon"><svg width="18" height="30" viewBox="0 0 18 30" fill="none" stroke="#1f86c6" stroke-width="5"><path d="M3 3l12 12L3 27"/></svg></span><span class="label">Speakers</span><svg width="24" height="26" viewBox="0 0 24 26" fill="none" stroke="#999" stroke-width="4"><path d="M3 12l9-9 9 9M3 23l9-9 9 9"/></svg></div>
  <div class="nav-item"><span class="icon"><svg width="18" height="30" viewBox="0 0 18 30" fill="none" stroke="#1f86c6" stroke-width="5"><path d="M3 3l12 12L3 27"/></svg></span><span class="label">Track</span><svg width="24" height="26" viewBox="0 0 24 26" fill="none" stroke="#777" stroke-width="4"><path d="M3 3l9 9 9-9M3 14l9 9 9-9"/></svg></div>

  <section class="track-body">
    <div class="track-card">
      <div class="card-head">
        <svg width="50" height="38" viewBox="0 0 50 38" fill="#555"><rect x="0" y="2" width="30" height="24" rx="2"/><path d="M32 10h10l8 9v7H32z"/><circle cx="10" cy="30" r="6"/><circle cx="40" cy="30" r="6"/></svg>
        <span>Track Details</span>
      </div>
      <div class="card-body">
        <div class="field-label">Track Name :</div>
        <div class="field-input">This is a required field</div>
        <button class="btn-add">Add Track</button>
      </div>
    </div>
  </section>

  <div class="nav-item"><span class="icon"><svg width="18" height="30" viewBox="0 0 18 30" fill="none" stroke="#1f86c6" stroke-width="5"><path d="M3 3l12 12L3 27"/></svg></span><span class="label">Sessions</span><svg width="24" height="26" viewBox="0 0 24 26" fill="none" stroke="#999" stroke-width="4"><path d="M3 12l9-9 9 9M3 23l9-9 9 9"/></svg></div>
  <div class="nav-item"><span class="icon"><svg width="18" height="30" viewBox="0 0 18 30" fill="none" stroke="#1f86c6" stroke-width="5"><path d="M3 3l12 12L3 27"/></svg></span><span class="label">Organizers</span><svg width="24" height="26" viewBox="0 0 24 26" fill="none" stroke="#999" stroke-width="4"><path d="M3 12l9-9 9 9M3 23l9-9 9 9"/></svg></div>
  <div class="nav-item"><span class="icon"><svg width="18" height="30" viewBox="0 0 18 30" fill="none" stroke="#1f86c6" stroke-width="5"><path d="M3 3l12 12L3 27"/></svg></span><span class="label">Sponsors</span><svg width="24" height="26" viewBox="0 0 24 26" fill="none" stroke="#999" stroke-width="4"><path d="M3 12l9-9 9 9M3 23l9-9 9 9"/></svg></div>
  <div class="nav-item"><span class="icon"><svg width="18" height="30" viewBox="0 0 18 30" fill="none" stroke="#1f86c6" stroke-width="5"><path d="M3 3l12 12L3 27"/></svg></span><span class="label">Exhibitor</span><svg width="24" height="26" viewBox="0 0 24 26" fill="none" stroke="#999" stroke-width="4"><path d="M3 12l9-9 9 9M3 23l9-9 9 9"/></svg></div>
  <div class="nav-item"><span class="icon"><svg width="18" height="30" viewBox="0 0 18 30" fill="none" stroke="#1f86c6" stroke-width="5"><path d="M3 3l12 12L3 27"/></svg></span><span class="label">Security</span><svg width="24" height="26" viewBox="0 0 24 26" fill="none" stroke="#999" stroke-width="4"><path d="M3 12l9-9 9 9M3 23l9-9 9 9"/></svg></div>
  <div class="nav-item"><span class="icon"><svg width="18" height="30" viewBox="0 0 18 30" fill="none" stroke="#1f86c6" stroke-width="5"><path d="M3 3l12 12L3 27"/></svg></span><span class="label">Members</span><svg width="24" height="26" viewBox="0 0 24 26" fill="none" stroke="#999" stroke-width="4"><path d="M3 12l9-9 9 9M3 23l9-9 9 9"/></svg></div>
</nav>

<footer class="site-footer">
  <div class="social-row"><span></span><span></span><span></span><span></span><span></span></div>
  <div class="footer-links">Home<span class="sep">/</span>Contact<span class="sep">/</span>Topics<span class="sep">/</span>Posts &amp; Comments<span class="sep">/</span>Videos Links</div>
  <div class="copyright">Copyright @ 2015 - 2015.Teamora. All Rights Reserved.</div>
</footer>
</body>
</html>
```